Quendle Pools & Patio Homepage Design

I am looking for someone to design a one-page website for a company called Quendle Pools & Patio. While the content will be different, the design should be similar to https://quendle-example.com/pools-patio/.
Industry/Entity Type
Pool Cleaning Service
Number of Pages Required
1 page
Font styles to use
Other font styles liked:
- See brand guidelines

Requirements
Must have
- Must be similar in style https://quendle-example.com/pools-patio/. Look at the Word Doc for the content.

```html
<!DOCTYPE html>
<html lang="en">
<head>
<meta charset="utf-8">
<title>Quendle Pools &amp; Patio</title>
<link rel="stylesheet" href="https://fonts.googleapis.com/css2?family=Barlow:wght@400;500;600;800&display=swap">
<style>
:root{
  --sky:#3a9de0;
  --navy:#0a3d78;
  --ink:#1d4677;
  --green:#2bd964;
  --mist:#eef2f6;
  --blush:#f8f6f7;
  --orange:#f39322;
  --line:#c9d3de;
  --muted:#7b8a9a;
}
*{box-sizing:border-box;margin:0;padding:0}
html,body{width:1200px;height:3059px;overflow:hidden;background:#fff}
body{position:relative;font-family:"Barlow",sans-serif;font-weight:400;color:var(--ink);-webkit-font-smoothing:antialiased}
.abs{position:absolute}
.hex{clip-path:polygon(50% 0,100% 25%,100% 75%,50% 100%,0 75%,0 25%)}
.hex-flat{clip-path:polygon(25% 0,75% 0,100% 50%,75% 100%,25% 100%,0 50%)}

.topbar{left:0;top:0;width:1200px;height:43px;background:var(--sky);color:#fff;font-weight:500;font-size:14px;display:flex;justify-content:center;align-items:center;gap:26px}
.topbar span{display:flex;align-items:center;gap:9px}
.topbar .sep{width:1px;height:20px;background:#fff}

.nav{left:0;top:43px;width:1200px;height:103px;background:#fff}
.brand{left:58px;top:28px;display:flex;align-items:center;gap:10px;font-weight:600;font-size:38px;color:var(--sky)}
.brand i{width:30px;height:30px;background:var(--green);display:block}
.menu{left:310px;top:36px;display:flex;gap:34px;font-size:18px;font-weight:500;color:var(--navy)}
.menu .on{font-weight:800;border-bottom:3px solid var(--navy);padding-bottom:6px}
.btn-out{left:816px;top:30px;width:99px;height:44px;border:2px solid var(--sky);color:var(--sky);font-size:14px;font-weight:600;display:flex;align-items:center;justify-content:center}
.btn-fill{left:922px;top:30px;width:130px;height:44px;background:var(--green);color:var(--navy);font-size:14px;font-weight:600;display:flex;align-items:center;justify-content:center}
.search{left:1112px;top:40px}

.hero{left:0;top:146px;width:1200px;height:500px;background:var(--navy);overflow:hidden}
.photo-pool{background:linear-gradient(160deg,#6cc6e8,#1a86c4 60%,#2e6b3f)}
.photo-deck{background:linear-gradient(170deg,#a8b6c2,#8a7560 45%,#4d9fc0)}
.photo-filter{background:linear-gradient(150deg,#7c7a76,#d9dde0 50%,#3b4b68)}
.photo-hose{background:linear-gradient(200deg,#a8c7d8,#3b7fb0 55%,#1e4f82)}
.hero h1{left:272px;top:136px;font-weight:800;font-size:56px;line-height:65px;color:#fff}
.hero h1 u{text-decoration:none;border-bottom:5px solid var(--green)}
.hero p{left:272px;top:348px;font-size:25px;color:#fff}

.quote-form{left:757px;top:419px;width:342px;height:375px;background:#fff;box-shadow:0 4px 18px rgba(10,61,120,.15);padding:24px 21px}
.field{border-bottom:1px solid var(--line);height:38px;font-size:13px;color:var(--muted);padding:12px 6px 0;margin-bottom:12px}
.row{display:flex;gap:12px}
.row .field{flex:1}
.field small{display:block;font-size:9px;margin-top:-8px}
.field b{font-weight:500;color:#222}
.contact-label{font-size:13px;color:var(--ink);margin-top:20px}
.radios{display:flex;justify-content:space-around;font-size:13px;color:var(--muted);margin-top:18px}
.radios span{display:flex;align-items:center;gap:7px}
.radios span::before{content:"";width:12px;height:12px;border:1px solid var(--ink);border-radius:50%}
.submit{margin:26px 10px 0;height:40px;background:var(--green);color:var(--navy);font-size:14px;font-weight:600;display:flex;align-items:center;justify-content:center}

.band{left:0;width:1200px}
.title{left:0;width:1200px;text-align:center;font-weight:800;font-size:40px;color:var(--navy)}
.rule{left:523px;width:155px;height:4px;background:var(--green)}
.overview-text{left:613px;top:991px;width:445px;font-size:15px;line-height:23.4px;color:var(--ink)}
.overview-text p+p{margin-top:16px}
.btn-arrow{left:613px;top:1321px;width:166px;height:40px;background:var(--green);color:#fff;font-weight:600;font-size:14px;display:flex;align-items:center;justify-content:center;gap:8px}

.service{width:300px;text-align:center;color:var(--ink)}
.service .pic{width:256px;height:294px;margin:0 auto;position:relative}
.service h3{font-weight:500;font-size:34px;color:var(--navy);margin-top:14px}
.service p,.service li{font-size:15px;line-height:19.5px;color:var(--ink)}
.service p{margin-top:10px;padding:0 10px}
.service ul{text-align:left;margin:6px 0 0 64px;list-style:none}
.service li{margin-top:2px}
.service li::before{content:"▪ ";font-size:11px;color:var(--sky)}
.badge{position:absolute;left:93px;top:200px;width:70px;height:80px;background:#fff;display:flex;align-items:center;justify-content:center}
.badge div{width:60px;height:68px;background:var(--orange);display:flex;align-items:center;justify-content:center}
.svc-btn{position:absolute;width:250px;height:40px;border:2px solid var(--sky);color:var(--sky);font-weight:600;font-size:14px;display:flex;align-items:center;justify-content:center}
.svc-btn.solid{background:var(--sky);color:#fff}

.tech-name{left:658px;top:2550px;font-weight:500;font-size:30px;color:var(--navy)}
.tech-quote{left:658px;top:2605px;font-weight:800;font-size:40px;color:var(--navy);line-height:1}
.tech-text{left:658px;top:2649px;width:300px;font-size:15px;line-height:21.6px;color:var(--ink)}
</style>
</head>
<body>

<div class="abs topbar">
  <span><svg width="16" height="18" viewBox="0 0 16 18" fill="none" stroke="#fff" stroke-width="1.5"><path d="M8 17s6-6 6-10A6 6 0 0 0 2 7c0 4 6 10 6 10z"/><circle cx="8" cy="7" r="2"/></svg>1180 Harbor Lane, Suite 410, Lakeview, TX 75990</span>
  <i class="sep"></i>
  <span><svg width="16" height="16" viewBox="0 0 16 16" fill="none" stroke="#fff" stroke-width="1.5"><path d="M3 1h3l1.5 4-2 1.5a9 9 0 0 0 4 4L11 8.5l4 1.5v3a2 2 0 0 1-2 2A13 13 0 0 1 1 3a2 2 0 0 1 2-2z"/></svg>555-204-7719</span>
  <i class="sep"></i>
  <span><svg width="18" height="14" viewBox="0 0 18 14" fill="none" stroke="#fff" stroke-width="1.5"><rect x="1" y="1" width="16" height="12"/><path d="M1 1l8 7 8-7"/></svg>marketing@quendle-example.com</span>
</div>

<header class="abs nav">
  <div class="abs brand"><i></i>quendle</div>
  <nav class="abs menu">
    <span class="on">About Us ▾</span><span>Services ▾</span><span>Learn</span><span>Location</span><span>FAQs</span>
  </nav>
  <div class="abs btn-out">SIGN IN</div>
  <div class="abs btn-fill">GET A QUOTE</div>
  <svg class="abs search" width="24" height="24" viewBox="0 0 24 24" fill="none" stroke="#0a3d78" stroke-width="2"><circle cx="10" cy="10" r="8"/><path d="M16 16l6 6"/></svg>
</header>

<section class="abs hero">
  <div class="abs hex-flat photo-pool" role="img" aria-label="Child playing in a backyard pool" style="left:-120px;top:-80px;width:250px;height:220px"></div>
  <div class="abs hex-flat photo-deck" role="img" aria-label="Technician skimming a pool beside a covered patio" style="left:10px;top:110px;width:230px;height:265px"></div>
  <div class="abs hex-flat photo-pool" role="img" aria-label="Pool with garden and ladder" style="left:-120px;top:330px;width:240px;height:220px"></div>
  <div class="abs hex-flat photo-pool" role="img" aria-label="Backyard pool with lawn" style="left:860px;top:-70px;width:240px;height:215px"></div>
  <div class="abs photo-deck" role="img" aria-label="Wooden deck with pool hose" style="left:1105px;top:0;width:95px;height:140px"></div>
  <div class="abs hex-flat photo-filter" role="img" aria-label="Technician holding a pool filter cartridge" style="left:737px;top:110px;width:235px;height:220px"></div>
  <div class="abs hex-flat photo-hose" role="img" aria-label="Pool vacuum head and hose in water" style="left:985px;top:110px;width:240px;height:260px"></div>
  <div class="abs hex-flat photo-pool" role="img" aria-label="Pool edge being cleaned" style="left:1105px;top:340px;width:160px;height:170px"></div>
  <h1 class="abs">Keep Your Pool<br>Sparkling With<br><u>Quendle!</u></h1>
  <p class="abs">Let Us Take Your Chores Off Your Plate</p>
</section>

<section class="abs band" style="top:646px;height:799px;background:var(--mist)">
  <svg class="abs" style="left:0;top:0" width="176" height="200"><polygon points="0,0 176,0 176,100 0,200" fill="#dbe4ec"/></svg>
</section>

<form class="abs quote-form">
  <div class="row"><div class="field"><small>First Name</small><b>Priya</b></div><div class="field">Last Name</div></div>
  <div class="field">Address</div>
  <div class="field">Phone</div>
  <div class="field">Email</div>
  <div class="contact-label">Preffered Contact Method:</div>
  <div class="radios"><span>Call</span><span>Text</span><span>Email</span></div>
  <div class="submit">GET QUOTE</div>
</form>

<h2 class="abs title" style="top:870px">Company Overview</h2>
<div class="abs rule" style="top:938px"></div>
<svg class="abs" style="left:172px;top:992px" width="180" height="362"><polyline points="156,0 0,90 0,272 156,362" fill="none" stroke="#0a3d78" stroke-width="1.5"/></svg>
<div class="abs hex photo-deck" role="img" aria-label="Technician skimming a pool beside a covered patio" style="left:220px;top:983px;width:324px;height:375px"></div>
<div class="abs overview-text">
  <p>We're Quendle Pools &amp; Patio, and we specialize in pool cleaning and repair services that will keep your pool looking its best. Our reliable and professional team is committed to helping you get the most out of your backyard oasis, ensuring it's always ready for all types of fun when you want it. Our weekly pool cleaning service is affordable and ensures that your pool is properly taken care of throughout the swimming season.</p>
  <p>When you choose us as your go-to for all things pools, relaxing days spent on a clean lounge chair are worry-free because we take care of all the hard work! From chemical balancing to scrubbing and filter maintenance - there's nothing too big or small for us. So don't wait any longer - trust Quendle to keep your pool sparkling all summer!</p>
</div>
<div class="abs btn-arrow">GET QUOTE <svg width="20" height="12" viewBox="0 0 20 12" fill="none" stroke="#fff" stroke-width="1.6"><path d="M0 6h18M13 1l5 5-5 5"/></svg></div>

<h2 class="abs title" style="top:1521px">Our Services</h2>
<div class="abs rule" style="top:1589px"></div>

<div class="abs service" style="left:94px;top:1631px">
  <div class="pic"><div class="hex photo-filter" role="img" aria-label="Technician rinsing a pool filter cartridge" style="width:256px;height:294px"></div>
    <div class="badge hex"><div class="hex"><svg width="34" height="30" viewBox="0 0 34 30" fill="none" stroke="#fff" stroke-width="2"><path d="M9 22V5a3 3 0 0 1 6 0M21 22V5a3 3 0 0 1 6 0M9 10h12M9 16h12M2 24q4 3 8 0t8 0 8 0 8 0M2 29q4 3 8 0t8 0 8 0 8 0"/></svg></div></div></div>
  <h3>Pool Maintenance</h3>
  <p>We perform regular checks on all your pool equipment to make sure it runs efficiently and safely.</p>
</div>
<div class="abs svc-btn" style="left:119px;top:2073px">GET QUOTE</div>

<div class="abs service" style="left:450px;top:1631px">
  <div class="pic"><div class="hex photo-pool" role="img" aria-label="Gloved hand holding chlorine tablets above a pool" style="width:256px;height:294px"></div>
    <div class="badge hex"><div class="hex"><svg width="34" height="30" viewBox="0 0 34 30" fill="none" stroke="#fff" stroke-width="2"><path d="M9 22V5a3 3 0 0 1 6 0M21 22V5a3 3 0 0 1 6 0M9 10h12M9 16h12M2 24q4 3 8 0t8 0 8 0 8 0M2 29q4 3 8 0t8 0 8 0 8 0"/></svg></div></div></div>
  <h3>Pool Cleaning</h3>
  <p style="margin-top:10px">Our weekly service includes,</p>
  <ul><li>chemical balancing,</li><li>debris removal,</li><li>wall and step scrubbing, and</li><li>filter maintenance.</li></ul>
  <p style="margin-top:8px;padding:0 50px">Standard chemicals are included in the quoted price.</p>
</div>
<div class="abs svc-btn solid" style="left:475px;top:2173px">GET QUOTE</div>

<div class="abs service" style="left:805px;top:1631px">
  <div class="pic"><div class="hex photo-hose" role="img" aria-label="Pool vacuum head and coiled hose underwater" style="width:256px;height:294px"></div>
    <div class="badge hex"><div class="hex"><svg width="34" height="30" viewBox="0 0 34 30" fill="none" stroke="#fff" stroke-width="2"><path d="M9 22V5a3 3 0 0 1 6 0M21 22V5a3 3 0 0 1 6 0M9 10h12M9 16h12M2 24q4 3 8 0t8 0 8 0 8 0M2 29q4 3 8 0t8 0 8 0 8 0"/></svg></div></div></div>
  <h3>Pool Repair</h3>
  <p>From plumbing to equipment malfunctions, our qualified technicians can diagnose and repair any pool problem you may have.</p>
</div>
<div class="abs svc-btn" style="left:831px;top:2092px">GET QUOTE</div>

<section class="abs band" style="top:2298px;height:591px;background:var(--blush)"></section>
<h2 class="abs title" style="top:2373px">Meet Your Technician</h2>
<div class="abs rule" style="top:2441px"></div>
<svg class="abs" style="left:261px;top:2535px" width="150" height="272"><polyline points="120,0 0,70 0,200 120,270" fill="none" stroke="#2bd964" stroke-width="1.5"/></svg>
<div class="abs hex" style="left:293px;top:2535px;width:249px;height:270px;background:var(--green)"></div>
<div class="abs hex" role="img" aria-label="Portrait photo of technician Dale Marlow" style="left:307px;top:2551px;width:221px;height:240px;background:linear-gradient(180deg,#b9c3cd,#7f8c9a)"></div>
<div class="abs" style="left:600px;top:2519px;width:1px;height:287px;background:var(--navy)"></div>
<div class="abs tech-name">Dale Marlow</div>
<div class="abs tech-quote">“</div>
<p class="abs tech-text">I understand that keeping your pool clean and well-maintained is a priority for you, which is why I'm committed to providing top-notch pool cleaning and repair services. Let's get started!</p>

<h2 class="abs title" style="top:2966px">Service Areas</h2>
<div class="abs rule" style="top:3033px"></div>

</body>
</html>
```